Billboard design 8x3M RAVU (Spanish company)

We´re located in the south of Spain. We run a local telecom company.
We sell Fiber optic, and mobile phone lines mainly.
The billboard will have to be in Spanish, I would like the price to be something you spot on first sight when passing by in the car.
Our company color is blue, like in our logo which I will add. I will also add a example from what we currently have.
The new offer should be:
1000 megas + 100Gigas movil con llamadas ilimitadas. (meaning 1000Mb fiber optic speed and 100Gb data and unlimited calls for 1 mobile line)
Our details are: phone line 958 47 6620
Website: ra-vu.es

```html
<!DOCTYPE html>
<html lang="es">
<head>
<meta charset="utf-8">
<title>RAVU – Valla 8x3</title>
<link rel="stylesheet" href="https://fonts.googleapis.com/css2?family=Montserrat:wght@600;700;800;900&display=swap">
<style>
  :root {
    --navy: #0b3a5c;
    --deep-blue: #075a8f;
    --mid-blue: #0d7fc2;
    --sky-blue: #2fb0e8;
    --orange: #f8aa22;
    --price-orange: #f6ab2f;
    --white: #ffffff;
    --stage: #e9edf1;
  }
  * { margin: 0; padding: 0; box-sizing: border-box; }
  html, body { width: 1200px; height: 874px; overflow: hidden; }
  body {
    background: var(--stage);
    font-family: "Montserrat", sans-serif;
    position: relative;
  }
  .billboard {
    position: absolute;
    left: 20px; top: 231px;
    width: 1160px; height: 412px;
    overflow: hidden;
  }
  .billboard-bg { position: absolute; inset: 0; }
  .price-block {
    position: absolute;
    left: 20px; top: 110px;
    width: 230px;
    text-align: center;
    color: var(--navy);
  }
  .price {
    font-weight: 900;
    font-size: 104px;
    line-height: 1;
    color: var(--price-orange);
    letter-spacing: -4px;
    text-shadow: 4px 5px 0 var(--navy);
  }
  .price-label {
    font-weight: 800;
    font-size: 34px;
    margin-top: 4px;
  }
  .brand {
    position: absolute;
    left: 360px; top: 22px;
    width: 400px;
    text-align: center;
    color: var(--white);
  }
  .brand-name {
    font-weight: 800;
    font-size: 92px;
    line-height: 1;
    letter-spacing: 6px;
  }
  .brand-services {
    font-weight: 700;
    font-size: 25px;
    margin-top: 12px;
    letter-spacing: 0.5px;
  }
  .website {
    position: absolute;
    left: 360px; top: 193px;
    width: 400px;
    text-align: center;
    color: var(--white);
    font-weight: 800;
    font-size: 22px;
    letter-spacing: 13px;
  }
  .phone-pill {
    position: absolute;
    left: 344px; top: 236px;
    width: 437px; height: 58px;
    border-radius: 29px;
    background: var(--navy);
    display: flex;
    align-items: center;
    gap: 12px;
    padding-left: 14px;
    color: var(--white);
  }
  .phone-icon { width: 40px; height: 40px; flex: none; }
  .phone-number {
    font-weight: 800;
    font-size: 50px;
    letter-spacing: 1px;
  }
  .illustration {
    position: absolute;
    left: 770px; top: 10px;
    width: 370px; height: 300px;
    border-radius: 40% 30% 10% 20%;
    background: radial-gradient(ellipse at 55% 60%, #ff7a12 0%, #f79b2c 45%, rgba(47,176,232,0) 75%);
  }
  .offer-band {
    position: absolute;
    left: 0; bottom: 0;
    width: 100%; height: 96px;
    background: var(--orange);
    display: flex;
    align-items: center;
    padding-left: 26px;
    color: var(--navy);
    gap: 14px;
  }
  .offer-main { font-weight: 800; font-size: 44px; letter-spacing: -0.5px; }
  .offer-sub { font-weight: 800; font-size: 27px; }
</style>
</head>
<body>
  <section class="billboard">
    <svg class="billboard-bg" width="1160" height="412" viewBox="0 0 1160 412" aria-hidden="true">
      <defs>
        <linearGradient id="panelBlue" x1="0" y1="0" x2="1" y2="0">
          <stop offset="0" stop-color="#064a78"/>
          <stop offset="0.45" stop-color="#0d7fc2"/>
          <stop offset="1" stop-color="#34b6ec"/>
        </linearGradient>
      </defs>
      <rect width="1160" height="412" fill="url(#panelBlue)"/>
      <path d="M0 0 H285 C360 40 390 200 330 316 H0 Z" fill="#0b5f97"/>
      <path d="M0 0 H255 C330 40 360 200 300 316 H0 Z" fill="#0b3a5c"/>
      <path d="M0 0 H225 C300 40 330 200 272 316 H0 Z" fill="#ffffff"/>
    </svg>

    <div class="price-block">
      <div class="price">35€</div>
      <div class="price-label">Por sólo</div>
    </div>

    <div class="brand">
      <div class="brand-name">RAVU</div>
      <div class="brand-services">Wifi | Fibra | Movil | Tv</div>
    </div>

    <div class="website">www.ra-vu.es</div>

    <div class="phone-pill">
      <svg class="phone-icon" viewBox="0 0 40 40" aria-hidden="true">
        <circle cx="20" cy="20" r="19" fill="#ffffff"/>
        <path d="M14 10 l4 5 -2.5 2.5 c1.5 3 3.5 5 6.5 6.5 L24.5 21.5 l5 4 -2.5 3.5 c-8 -1 -15 -8 -16 -16 Z" fill="#0b3a5c"/>
      </svg>
      <span class="phone-number">958 47 6620</span>
    </div>

    <div class="illustration" role="img" aria-label="Ilustración de un cohete despegando de un portátil entre una explosión de humo naranja"></div>

    <div class="offer-band">
      <span class="offer-main">1000 MEGAS + 100GIGAS</span>
      <span class="offer-sub">MOVIL CON LLAMADAS ILIMITADAS</span>
    </div>
  </section>
</body>
</html>
```